Redesign of business card for Cedar Ridge Mechanical

We are looking for a new design for our business cards for Cedar Ridge Mechanical. We are a plumbing & HVAC construction company, operating on the West Coast of Canada and USA. Logo attached.
Industry/Entity Type
Construction - Plumbing & HVAC
Contact Information for Business Card
Name, address, phone numbers, email, website address
Look and feel
Each slider illustrates characteristics of the customer's brand and the style your logo design should communicate.

```html
<!DOCTYPE html>
<html lang="en">
<head>
<meta charset="utf-8">
<title>Cedar Ridge Mechanical — Business Card</title>
<link rel="stylesheet" href="https://fonts.googleapis.com/css2?family=Poppins:wght@300;400;600&display=swap">
<style>
  :root {
    --stage: #222223;
    --card: #1f1f21;
    --ink: #f2f2f2;
    --ink-soft: #d9d9d9;
    --band: #ececec;
    --band-line: #1f1f21;
  }
  * { box-sizing: border-box; margin: 0; padding: 0; }
  html, body {
    width: 1200px; height: 780px; overflow: hidden;
    background: var(--stage);
    font-family: "Poppins", sans-serif;
    color: var(--ink);
  }
  .canvas {
    position: relative; width: 1200px; height: 780px;
    display: flex; align-items: center; justify-content: center; gap: 50px;
  }
  .card {
    position: relative; width: 525px; height: 300px;
    background: var(--card); border-radius: 22px; overflow: hidden;
    box-shadow: 0 18px 40px rgba(0,0,0,.45);
  }

  /* Back: contact side */
  .card__swoosh { position: absolute; inset: 0; }
  .card__brand {
    position: absolute; left: 44px; top: 40px; width: 170px;
    display: flex; align-items: flex-start; gap: 10px;
  }
  .brand-mark {
    flex: none; width: 14px; height: 14px; margin-top: 5px;
    background: var(--ink);
  }
  .brand-name {
    font-weight: 600; font-size: 17px; line-height: 1.2;
    letter-spacing: .02em; text-transform: uppercase; color: var(--ink);
  }
  .card__divider {
    position: absolute; left: 232px; top: 52px; width: 1px; height: 200px;
    background: var(--ink-soft);
  }
  .card__details { position: absolute; left: 258px; top: 54px; right: 20px; }
  .person__name { font-size: 26px; line-height: 1.1; font-weight: 300; }
  .person__name strong { font-weight: 600; }
  .person__role { font-size: 13px; font-weight: 400; margin-top: 2px; }
  .address { font-size: 12.5px; font-weight: 300; line-height: 1.45; margin-top: 12px; }
  .contact { list-style: none; margin-top: 12px; font-size: 12.5px; font-weight: 300; }
  .contact li { display: flex; align-items: center; gap: 8px; line-height: 1.55; }
  .contact svg { width: 11px; height: 11px; flex: none; fill: var(--ink); }

  /* Front: brand side */
  .card--front { display: flex; align-items: center; justify-content: center; }
  .front-brand { display: flex; align-items: center; gap: 18px; }
  .front-brand .brand-mark { width: 22px; height: 22px; margin: 0; }
  .front-brand .brand-name { font-size: 30px; line-height: 1.15; }
</style>
</head>
<body>
<main class="canvas">
  <section class="card card--back" aria-label="Business card, contact side">
    <svg class="card__swoosh" viewBox="0 0 525 300" preserveAspectRatio="none" aria-hidden="true">
      <path d="M0 40 C 20 150, 120 250, 525 300 L0 300 Z" fill="var(--band)"/>
      <path d="M20 150 C 80 240, 220 280, 525 296" fill="none" stroke="var(--band-line)" stroke-width="2.5"/>
    </svg>

    <div class="card__brand">
      <span class="brand-mark"></span>
      <span class="brand-name">Cedar Ridge Mechanical</span>
    </div>

    <div class="card__divider"></div>

    <div class="card__details">
      <h1 class="person__name"><strong>Marta</strong> Kovale</h1>
      <p class="person__role">Founder &amp; CEO</p>
      <p class="address">418 Alder Lane, Suite 120<br>Bellingham, WA 98225</p>
      <ul class="contact">
        <li>
          <svg viewBox="0 0 24 24"><path d="M6.6 10.8a15 15 0 0 0 6.6 6.6l2.2-2.2a1 1 0 0 1 1-.25 11.4 11.4 0 0 0 3.6.57 1 1 0 0 1 1 1V20a1 1 0 0 1-1 1A17 17 0 0 1 3 4a1 1 0 0 1 1-1h3.5a1 1 0 0 1 1 1c0 1.25.2 2.45.57 3.6a1 1 0 0 1-.25 1z"/></svg>
          (360) 555-0147
        </li>
        <li>
          <svg viewBox="0 0 24 24"><path d="M2 5h20v14H2z M4 7v.4l8 5 8-5V7l-8 5z" fill-rule="evenodd"/></svg>
          info@cedarridgemech.com
        </li>
        <li>
          <svg viewBox="0 0 24 24"><circle cx="12" cy="12" r="10" fill="none" stroke="#f2f2f2" stroke-width="2"/><path d="M2 12h20M12 2c3 3 3 17 0 20M12 2c-3 3-3 17 0 20" fill="none" stroke="#f2f2f2" stroke-width="1.6"/></svg>
          www.cedarridgemech.com
        </li>
      </ul>
    </div>
  </section>

  <section class="card card--front" aria-label="Business card, brand side">
    <div class="front-brand">
      <span class="brand-mark"></span>
      <span class="brand-name">Cedar Ridge<br>Mechanical</span>
    </div>
  </section>
</main>
</body>
</html>
```